Marlow Veston Orthodontics Ecommerce

We need to design an ecommerce website for a medical device company that specializes in orthodontics. With being a medical company, we will need to have two experiences for when a user visits our site. One for a non-registered user that will not show an pricing for the products and the other for a registered user that will show the price of the product. Ideally we would like a clean, modern design that utilizes our colors and is also is mobile friendly.

The current website: marlowvestonortho.com may be used a guide for the type of content and colors we used, but does not need to adhere to it.

Main colors to keep are the ones in the logo. Red, Blue and White.

Target Market(s)

Orthodontists, Dental

Industry/Entity Type

It Company

Coding

Coded - Design and coding required

Font styles to use
Sans Serif

Colors

Designer to choose colors to be used in the design.

Requirements
Must have
• Homepage, Product Family page, Product page and Contact Us Page. The design should work with any PC or mobile device to keep the user experience consistent.
Nice to have
• The quibrel.com website has a great feel to it and it would be nice to have something similar. Also, video is starting to become a big part of what we use to advertise and educate users about our products. It would be nice if we can incorporate video we possible to give users the ability to view them.
Should not have
• The design should be easy for users to navigate and use to locate the product they are interested in. It should not be confusing or too cluttered were a user can get lost.

```html
<!DOCTYPE html>
<html lang="en">
<head>
<meta charset="utf-8">
<title>Marlow Veston Orthodontics</title>
<link href="https://fonts.googleapis.com/css2?family=Rokkitt:wght@500;600&family=Roboto:wght@300;400;500;700&display=swap" rel="stylesheet">
<style>
:root{
  --red:#ea1c2d;
  --blue:#1670c4;
  --ink:#222222;
  --text:#555555;
  --muted:#8a8a8a;
  --nav:#1e1e1e;
  --grey-panel:#eeeeee;
  --blue-panel:#eef6fd;
  --light-panel:#f6f6f6;
  --white:#ffffff;
  --silver-light:#f2f2f2;
  --silver-mid:#b9b9b9;
  --silver-dark:#7d7d7d;
}
*{box-sizing:border-box;margin:0;padding:0}
html,body{width:1200px;height:2326px;overflow:hidden;background:var(--white)}
body{font-family:"Roboto",Arial,sans-serif;color:var(--ink)}
.page{position:relative;width:1200px;height:2326px}

/* header */
.site-header{height:36px;background:var(--nav);display:flex;align-items:center;padding:0 160px;color:var(--white)}
.brand{display:flex;align-items:center;gap:8px;font-weight:700;font-size:13px;letter-spacing:.3px;color:var(--white)}
.brand-square{width:10px;height:10px;background:var(--red)}
.main-nav{display:flex;gap:30px;margin-left:auto;margin-right:40px;font-size:11px}
.header-icons{display:flex;gap:16px;align-items:center}
.header-icons svg{width:14px;height:14px;stroke:var(--white);fill:none;stroke-width:2}
.cart-count{position:relative;display:flex}
.cart-count::after{content:"";position:absolute;right:-3px;bottom:-2px;width:6px;height:6px;border-radius:50%;background:var(--red)}

/* hero */
.hero{position:relative;height:422px;background:#f1f1f1;overflow:hidden}
.hero-photo{position:absolute;inset:0;background:
  radial-gradient(ellipse 260px 200px at 78% 68%,#4f9fd6 0%,rgba(79,159,214,0) 100%),
  radial-gradient(ellipse 320px 160px at 66% 45%,#e3bdb5 0%,rgba(227,189,181,0) 100%),
  radial-gradient(ellipse 200px 260px at 96% 20%,#3f8fca 0%,rgba(63,143,202,0) 100%),
  linear-gradient(90deg,#f4f4f4 0%,#efefef 45%,#e4e4e4 100%)}
.hero-content{position:absolute;left:206px;top:128px}
.hero-title{font-family:"Rokkitt",Georgia,serif;font-variant:small-caps;font-weight:600;font-size:31px;line-height:42px;color:var(--ink);letter-spacing:.5px}
.hero-sub{font-size:12px;color:var(--text);margin-top:12px}
.btn-red{display:inline-block;margin-top:24px;background:var(--red);color:var(--white);font-family:"Rokkitt",Georgia,serif;font-variant:small-caps;font-size:13px;padding:12px 40px}
.play-icon{position:absolute;left:930px;top:208px}

/* products */
.products{height:414px;padding:50px 0 0 206px;position:relative}
.section-title{font-family:"Rokkitt",Georgia,serif;font-variant:small-caps;font-weight:600;font-size:30px;color:var(--ink)}
.carousel{position:relative;margin-top:16px;display:flex;gap:12px}
.carousel-arrow{position:absolute;top:100px;width:22px;height:22px;border-radius:50%;display:flex;align-items:center;justify-content:center}
.carousel-arrow.prev{left:-50px;background:var(--ink)}
.carousel-arrow.next{left:906px;background:var(--white);box-shadow:0 0 4px rgba(0,0,0,.25)}
.product-card{width:284px}
.product-image{position:relative;height:208px;background:#f3f3f3}
.product-image.mirror{background:radial-gradient(ellipse 110px 40px at 55% 58%,#c9c9c9 0%,#e4e4e4 55%,#f4f4f4 100%)}
.product-image.clear{background:radial-gradient(ellipse 120px 34px at 50% 45%,#dfe7ee 0%,#eef1f4 60%,#f6f6f6 100%)}
.product-image.iris{background:radial-gradient(ellipse 120px 38px at 55% 48%,#8c7bc4 0%,#7fb9c9 35%,#e9e9ee 75%,#f4f4f4 100%)}
.price-tag{position:absolute;left:16px;top:14px;color:var(--white);font-size:12px;font-weight:500;padding:5px 8px}
.price-tag.red{background:var(--red)}
.price-tag.blue{background:var(--blue)}
.product-bar{height:58px;margin-top:10px;display:flex;align-items:center;justify-content:space-between;padding:0 0 0 12px;font-size:22px;font-weight:300;color:var(--muted)}
.product-bar.featured{background:var(--red);color:var(--white);border:3px solid var(--red);padding-right:10px}
.cart-btn{width:44px;height:44px;display:flex;align-items:center;justify-content:center;background:var(--blue)}
.product-bar.featured .cart-btn{background:transparent;border:2px solid var(--white)}
.cart-btn svg{width:18px;height:18px;fill:none;stroke:var(--white);stroke-width:2}

/* feature rows */
.feature{display:flex;height:337px}
.feature-text{width:700px;padding:40px 0 0 160px}
.feature-text.right{width:713px;padding:40px 60px 0 50px}
.feature-image{flex:1}
.feature-title{font-size:30px;font-weight:300;color:var(--ink)}
.feature-title.blue{color:var(--blue)}
.feature-title.red{color:var(--red)}
.feature-name{font-size:15px;font-weight:500;margin-top:18px;color:var(--ink)}
.feature-desc{font-size:12px;line-height:20px;color:var(--text);margin-top:16px;max-width:500px}
.resources{font-size:11px;color:var(--ink);margin-top:14px}
.buy-row{display:flex;align-items:center;gap:22px;margin-top:22px}
.btn-outline{font-size:10px;font-weight:500;padding:9px 20px;border:2px solid var(--ink);color:var(--ink)}
.btn-outline.blue{border-color:var(--blue);color:var(--blue)}
.btn-outline.red{border-color:var(--red);color:var(--red)}
.price-label{font-size:12px;font-weight:700;display:flex;align-items:center;gap:10px}
.price-chip{color:var(--white);font-size:12px;padding:9px 10px}
.price-chip.dark{background:#2b2b2b}
.price-chip.blue{background:var(--blue)}
.price-chip.red{background:var(--red)}
.brackets{background:var(--grey-panel)}
.brackets .feature-image{margin:3px 0 0 6px;background:
  radial-gradient(ellipse 170px 140px at 50% 52%,var(--silver-mid) 0%,#a6a6a6 40%,rgba(200,200,200,0) 75%),
  linear-gradient(160deg,#e4e4e4,#c8c8c8)}
.ceramic .feature-image{flex:0 0 487px;background:
  radial-gradient(ellipse 170px 120px at 50% 50%,#c4daf0 0%,#d6e8f9 50%,rgba(222,236,251,0) 80%),
  linear-gradient(160deg,#e7f2fd,#d4e7f9)}
.ceramic .feature-text{background:var(--blue-panel)}
.halden{background:var(--light-panel)}
.halden .feature-image{background:
  radial-gradient(ellipse 170px 110px at 50% 50%,#a4a4a8 0%,#c3bfc2 40%,rgba(250,222,229,0) 75%),
  linear-gradient(160deg,#fde6eb,#f8d6dd)}

/* footer */
.site-footer{position:relative;height:442px;background:linear-gradient(180deg,#1b1b1b,#0e0e0e);color:#cfcfcf;padding:44px 0 0 160px}
.footer-cols{display:flex}
.footer-col{width:252px}
.footer-col h4{font-size:12px;font-weight:500;color:var(--white);letter-spacing:.3px;margin-bottom:12px}
.footer-col li{list-style:none;font-size:10.5px;line-height:20px;color:#bdbdbd;position:relative;padding-left:12px}
.footer-col li::before{content:"";position:absolute;left:0;top:8px;width:4px;height:4px;background:var(--red)}
.address{margin-top:34px;font-size:10.5px;line-height:20px;color:#bdbdbd}
.address b{color:var(--white);font-weight:500;display:inline-block;width:58px}
.footer-brand{position:absolute;left:160px;top:314px;display:flex;align-items:center;gap:8px;font-size:13px;font-weight:700;color:var(--white)}
.copyright{position:absolute;left:806px;top:298px;font-size:10.5px;color:#bdbdbd}
.social{position:absolute;left:800px;top:340px;display:flex;gap:16px}
.social span{width:40px;height:40px;border-radius:50%;background:#2e2e2e;border:1px solid #555555}
</style>
</head>
<body>
<div class="page">

  <header class="site-header">
    <div class="brand"><span class="brand-square"></span>Marlow Veston Orthodontics</div>
    <nav class="main-nav">
      <span>Products</span><span>Education/Events</span><span>Practice Solutions</span><span>About Us</span><span>Resources</span><span>Contact Us</span>
    </nav>
    <div class="header-icons">
      <svg viewBox="0 0 24 24"><circle cx="12" cy="8" r="4"/><path d="M4 21c1-5 15-5 16 0"/></svg>
      <svg viewBox="0 0 24 24"><circle cx="10" cy="10" r="6"/><path d="M15 15l6 6"/></svg>
      <span class="cart-count"><svg viewBox="0 0 24 24"><path d="M5 8h14l-1 13H6z"/><path d="M9 8V6a3 3 0 0 1 6 0v2"/></svg></span>
    </div>
  </header>

  <section class="hero">
    <div class="hero-photo" role="img" aria-label="Gloved hands holding a dental model with braces and an instrument"></div>
    <div class="hero-content">
      <h1 class="hero-title">Orthodontic Excellence &amp; Technolog<br>Value, Quality, Innovation</h1>
      <p class="hero-sub">Empowering Your Future With Revolutionary Products</p>
      <span class="btn-red">Watch Video</span>
    </div>
    <svg class="play-icon" width="36" height="44" viewBox="0 0 36 44"><path d="M3 3l30 19L3 41z" fill="none" stroke="#ea1c2d" stroke-width="3"/></svg>
  </section>

  <section class="products">
    <h2 class="section-title">Intraoral Products</h2>
    <div class="carousel">
      <span class="carousel-arrow prev"><svg width="8" height="8" viewBox="0 0 8 8"><path d="M5 1L2 4l3 3" fill="none" stroke="#fff" stroke-width="1.5"/></svg></span>
      <article class="product-card">
        <div class="product-image mirror" role="img" aria-label="Silver intraoral appliance with a curved handle"><span class="price-tag red">$ 28.00</span></div>
        <div class="product-bar featured">Patient Financing<span class="cart-btn"><svg viewBox="0 0 24 24"><path d="M5 8h14l-1 13H6z"/><path d="M9 8V6a3 3 0 0 1 6 0v2"/></svg></span></div>
      </article>
      <article class="product-card">
        <div class="product-image clear" role="img" aria-label="Clear plastic motion appliance"><span class="price-tag blue">$ 28.00</span></div>
        <div class="product-bar">Cavalla Motion...<span class="cart-btn"><svg viewBox="0 0 24 24"><path d="M5 8h14l-1 13H6z"/><path d="M9 8V6a3 3 0 0 1 6 0v2"/></svg></span></div>
      </article>
      <article class="product-card">
        <div class="product-image iris" role="img" aria-label="Iridescent metal motion 3D appliance"><span class="price-tag blue">$ 28.00</span></div>
        <div class="product-bar">Cavalla Motion 3D<span class="cart-btn"><svg viewBox="0 0 24 24"><path d="M5 8h14l-1 13H6z"/><path d="M9 8V6a3 3 0 0 1 6 0v2"/></svg></span></div>
      </article>
      <span class="carousel-arrow next"><svg width="8" height="8" viewBox="0 0 8 8"><path d="M3 1l3 3-3 3" fill="none" stroke="#222" stroke-width="1.5"/></svg></span>
    </div>
  </section>

  <section class="feature brackets">
    <div class="feature-text">
      <h3 class="feature-title">Brackets</h3>
      <p class="feature-name">VLR™ Self-Ligating Bracket</p>
      <p class="feature-desc">Introducing the completely re-engineered VLR Self-Ligating Appliance System. The VLR Bracket System resets the standards for excellence and performance in passive self-ligating brackets with numerous clinician driven innovations for clinical effectiveness and efficiency.</p>
      <p class="resources">Resources +</p>
      <div class="buy-row"><span class="btn-outline">BUY NOW</span><span class="price-label">Price :<span class="price-chip dark">$ 28.00</span></span></div>
    </div>
    <div class="feature-image" role="img" aria-label="Close-up of a silver self-ligating bracket"></div>
  </section>

  <section class="feature ceramic">
    <div class="feature-image" role="img" aria-label="Clear sapphire ceramic bracket"></div>
    <div class="feature-text right">
      <h3 class="feature-title blue">Ceramic Bracket System</h3>
      <p class="feature-name">ClearVale Plus™ Sapphire Ceramic Bracket System</p>
      <p class="feature-desc">Developed to provide unparalleled performance and crystal clear transparency, the ClearVale Plus Sapphire Ceramic Bracket is manufactured from a single crystal sapphire, one of the hardest and clearest materials found in nature. The result is an aesthetic bracket that allows the natural tooth tone to show through, regardless of the</p>
      <p class="resources">Resources +</p>
      <div class="buy-row"><span class="btn-outline blue">BUY NOW</span><span class="price-label">Price :<span class="price-chip blue">$ 28.00</span></span></div>
    </div>
  </section>

  <section class="feature halden">
    <div class="feature-text">
      <h3 class="feature-title red">Halden - 2;™ Appliance</h3>
      <p class="feature-name">Halden2;™ Appliance</p>
      <p class="feature-desc">Building upon the original Straight Wire Appliance, the Halden Foundation™, collaborated with us to develop an improved appliance system which has been through 20 years of research and development. We are the proud, exclusive manufacturer and distributor of the Halden2; Appliance.</p>
      <p class="resources">Resources +</p>
      <div class="buy-row"><span class="btn-outline red">BUY NOW</span><span class="price-label">Price :<span class="price-chip red">$ 28.00</span></span></div>
    </div>
    <div class="feature-image" role="img" aria-label="Silver straight wire appliance bracket"></div>
  </section>

  <footer class="site-footer">
    <div class="footer-cols">
      <div class="footer-col">
        <h4>CONTACT US</h4>
        <ul><li>US Sales</li><li>International Sales</li><li>Subscribe to E-News</li></ul>
        <p class="address">418 Brindle Ave.<br>Oceanside, CA 92054-1100<br><b>Toll Free</b>: 800.555.0142<br><b>Phone</b>: 760.555.0178<br><b>Fax</b>: 760.555.0179</p>
      </div>
      <div class="footer-col">
        <h4>PRODUCTS</h4>
        <ul><li>Brackets</li><li>Bands &amp; Buccal Tubes</li><li>Adhesives &amp; Cements</li><li>Archwires</li><li>Elastomerics</li><li>Intraoral Products</li><li>Mini Screws - TAD's</li><li>Pliers &amp; Instruments</li><li>General Supplies</li><li>Patient Supplies</li><li>OSA</li></ul>
      </div>
      <div class="footer-col">
        <h4>PRACTICE SOLUTIONS</h4>
        <ul><li>Grad Programs</li><li>Financial Solutions</li><li>MVO Buying Club</li><li>Practice Marketing</li></ul>
      </div>
      <div class="footer-col">
        <h4>ABOUT US</h4>
        <ul><li>Mission Statement</li><li>Social Responsibility</li><li>Company Governance</li><li>Careers</li><li>Executive Bios</li><li>Announcements</li><li>Company History</li></ul>
      </div>
    </div>
    <div class="footer-brand"><span class="brand-square"></span>Marlow Veston Orthodontics</div>
    <p class="copyright">© 2018 Marlow Veston Ortho All rights are Reserved.</p>
    <div class="social" aria-label="Social links"><span></span><span></span><span></span><span></span></div>
  </footer>

</div>
</body>
</html>
```